KORV PTY LTD - Business Cards

Design a modern business card - using the attached Designs.
Same design as on the front, apart from the names/numbers/emails to be different.
We want the cards to be very glossy to stand out, do I think the simple black/white/metallic will be effective.
Both lots of details below:

Tom Wrenshaw
Director
tom_korv@nulvane.com
0438 274 093

Lewis Corbyn
Director
lewis_korv@nulvane.com
0419 385 642

Industry/Entity Type

Business

```html
<!DOCTYPE html>
<html lang="en">
<head>
<meta charset="utf-8">
<title>KORV PTY LTD – Business Cards</title>
<link rel="stylesheet" href="https://fonts.googleapis.com/css2?family=Carlito:wght@400;700&display=swap">
<style>
  :root {
    --page: #ffffff;
    --carbon-dark: #121212;
    --carbon-mid: #2a2a2a;
    --metal-light: #d8d8d8;
    --metal-mid: #8d8d8d;
    --metal-dark: #4a4a4a;
    --band: #2e2e2e;
    --text-white: #f2f2f2;
    --text-grey: #8a8a8a;
    --text-phone: #9a9a9a;
  }
  html, body {
    margin: 0;
    width: 1200px;
    height: 1000px;
    overflow: hidden;
    background: var(--page);
    font-family: "Carlito", "Calibri", sans-serif;
  }
  .card {
    position: absolute;
    left: 368px;
    width: 448px;
    height: 263px;
    overflow: hidden;
    box-shadow: 0 2px 5px rgba(0,0,0,.35);
  }
  .card--front { top: 62px; }
  .card--lewis { top: 364px; }
  .card--tom { top: 679px; }
  .card svg { position: absolute; inset: 0; display: block; }
  .wordmark {
    position: absolute;
    margin: 0;
    color: var(--text-white);
    font-weight: 700;
    letter-spacing: 3px;
    line-height: 1;
    transform: translate(-50%, -50%);
  }
  .card--front .wordmark { left: 221px; top: 131px; font-size: 46px; color: #1d1d1d; }
  .card--back .wordmark { left: 347px; top: 138px; font-size: 34px; }
  .contact {
    position: absolute;
    left: 51px;
    top: 63px;
    line-height: 1;
  }
  .contact__name { margin: 0; font-size: 18px; color: var(--text-white); }
  .contact__role { margin: 2px 0 0; font-size: 9px; color: var(--text-grey); }
  .contact__email { margin: 1px 0 0; font-size: 12px; color: var(--text-grey); }
  .contact__phone { margin: 5px 0 0; font-size: 16px; font-weight: 700; color: var(--text-phone); }
  .services {
    position: absolute;
    left: 52px;
    top: 152px;
    margin: 0;
    padding: 0;
    list-style: none;
    font-size: 9px;
    color: var(--text-white);
  }
  .services li { height: 12px; line-height: 12px; }
</style>
</head>
<body>

<svg width="0" height="0" style="position:absolute">
  <defs>
    <linearGradient id="carbon" x1="0" y1="0" x2="1" y2="1">
      <stop offset="0" stop-color="#262626"/>
      <stop offset=".5" stop-color="#161616"/>
      <stop offset="1" stop-color="#2a2a2a"/>
    </linearGradient>
    <linearGradient id="metal-plate" x1="0" y1="0" x2="0" y2="1">
      <stop offset="0" stop-color="#5a5a5a"/>
      <stop offset=".35" stop-color="#d4d4d4"/>
      <stop offset=".6" stop-color="#bdbdbd"/>
      <stop offset="1" stop-color="#4c4c4c"/>
    </linearGradient>
    <linearGradient id="metal-back" x1="0" y1="0" x2="0" y2="1">
      <stop offset="0" stop-color="#6a6a6a"/>
      <stop offset=".12" stop-color="#d0d0d0"/>
      <stop offset=".5" stop-color="#7a7a7a"/>
      <stop offset=".88" stop-color="#cfcfcf"/>
      <stop offset="1" stop-color="#5c5c5c"/>
    </linearGradient>
    <linearGradient id="name-band" x1="0" y1="0" x2="0" y2="1">
      <stop offset="0" stop-color="#3a3a3a"/>
      <stop offset="1" stop-color="#262626"/>
    </linearGradient>
  </defs>
</svg>

<!-- Front -->
<section class="card card--front">
  <svg viewBox="0 0 448 263" role="img" aria-label="Carbon fibre surface with a brushed metal plate">
    <rect width="448" height="263" fill="url(#carbon)"/>
    <rect x="108" y="0" width="226" height="263" fill="url(#metal-plate)"/>
    <rect x="107" y="0" width="1" height="263" fill="#000" opacity=".6"/>
    <rect x="334" y="0" width="1" height="263" fill="#000" opacity=".6"/>
    <g fill="#777" stroke="#333" stroke-width="1">
      <circle cx="124" cy="14" r="4.5"/>
      <circle cx="323" cy="14" r="4.5"/>
      <circle cx="122" cy="252" r="4.5"/>
      <circle cx="323" cy="252" r="4.5"/>
    </g>
  </svg>
  <p class="wordmark">KORV</p>
</section>

<!-- Back: Lewis Corbyn -->
<section class="card card--back card--lewis">
  <svg viewBox="0 0 448 263" aria-hidden="true">
    <rect width="448" height="263" fill="url(#metal-back)"/>
    <rect x="0" y="46" width="300" height="2" fill="#cfcfcf"/>
    <rect x="0" y="48" width="300" height="87" fill="url(#name-band)"/>
    <rect x="0" y="135" width="300" height="10" fill="#5a5a5a"/>
    <rect x="0" y="145" width="300" height="1" fill="#bdbdbd"/>
    <g fill="#444" opacity=".85">
      <rect x="0" y="152" width="255" height="11"/>
      <rect x="0" y="164" width="248" height="11"/>
      <rect x="0" y="176" width="250" height="11"/>
      <rect x="0" y="188" width="244" height="11"/>
      <rect x="0" y="200" width="246" height="11"/>
    </g>
    <g fill="#9a9a9a" stroke="#333" stroke-width="1">
      <circle cx="36" cy="157.5" r="4.5"/>
      <circle cx="36" cy="181.5" r="4.5"/>
      <circle cx="36" cy="205.5" r="4.5"/>
    </g>
    <polygon points="292,0 448,0 448,263 197,263" fill="url(#carbon)"/>
    <line x1="292" y1="0" x2="197" y2="263" stroke="#777" stroke-width="1"/>
  </svg>
  <div class="contact">
    <p class="contact__name">Lewis Corbyn</p>
    <p class="contact__role">Director</p>
    <p class="contact__email">lewis_korv@nulvane.com</p>
    <p class="contact__phone">0419 385 642</p>
  </div>
  <ul class="services">
    <li>Labour Hire</li>
    <li>Machine Shutdowns</li>
    <li>Preventative Maintence and Servicing</li>
    <li>Breakdown Repairs</li>
    <li>Contract Supervision</li>
  </ul>
  <p class="wordmark">KORV</p>
</section>

<!-- Back: Tom Wrenshaw -->
<section class="card card--back card--tom">
  <svg viewBox="0 0 448 263" aria-hidden="true">
    <rect width="448" height="263" fill="url(#metal-back)"/>
    <rect x="0" y="46" width="300" height="2" fill="#cfcfcf"/>
    <rect x="0" y="48" width="300" height="87" fill="url(#name-band)"/>
    <rect x="0" y="135" width="300" height="10" fill="#5a5a5a"/>
    <rect x="0" y="145" width="300" height="1" fill="#bdbdbd"/>
    <g fill="#444" opacity=".85">
      <rect x="0" y="152" width="255" height="11"/>
      <rect x="0" y="164" width="248" height="11"/>
      <rect x="0" y="176" width="250" height="11"/>
      <rect x="0" y="188" width="244" height="11"/>
      <rect x="0" y="200" width="246" height="11"/>
    </g>
    <g fill="#9a9a9a" stroke="#333" stroke-width="1">
      <circle cx="36" cy="157.5" r="4.5"/>
      <circle cx="36" cy="181.5" r="4.5"/>
      <circle cx="36" cy="205.5" r="4.5"/>
    </g>
    <polygon points="292,0 448,0 448,263 197,263" fill="url(#carbon)"/>
    <line x1="292" y1="0" x2="197" y2="263" stroke="#777" stroke-width="1"/>
  </svg>
  <div class="contact">
    <p class="contact__name">Tom Wrenshaw</p>
    <p class="contact__role">Director</p>
    <p class="contact__email">tom_korv@nulvane.com</p>
    <p class="contact__phone">0438 274 093</p>
  </div>
  <ul class="services">
    <li>Labour Hire</li>
    <li>Machine Shutdowns</li>
    <li>Preventative Maintence and Servicing</li>
    <li>Breakdown Repairs</li>
    <li>Contract Supervision</li>
  </ul>
  <p class="wordmark">KORV</p>
</section>

</body>
</html>
```